Road Construction Company needs business cards

We would like a new business card designed for our business.

We're a road construction company based in Qld, Australia.

Can the business card please have the following information on it.

Name: Warren Halbeck
Position: General Manager
Phone: 0472 915 348
Email: Warren.halbeck@tovrin.com.au
Address: 87 Marrow Ave, Pendlebay, QLD, 4023
Website: www.tovrin.com.au

Visually we'd like the card to be professional and simple.

Attached is our logo.

Our website is www.tovrin.com.au

Target Market(s)

Men aged 25-60

Contact Information for Business Card

As listed in project description

Font styles to use
Serif

Requirements
Must have
• Large logo on back of card

```html
<!DOCTYPE html>
<html lang="en">
<head>
<meta charset="utf-8">
<title>Tovrin Business Card</title>
<link rel="stylesheet" href="https://fonts.googleapis.com/css2?family=Open+Sans:wght@400;700;800&display=swap">
<style>
  :root {
    --brand-blue: #1457a8;
    --sky-blue: #3fa6da;
    --pale-blue: #e3eefa;
    --ink: #1c1c1c;
    --paper: #ffffff;
    --backdrop: #e6e7ea;
  }
  * { margin: 0; padding: 0; box-sizing: border-box; }
  html, body {
    width: 1200px; height: 780px; overflow: hidden;
    background: var(--backdrop);
    font-family: "Open Sans", sans-serif;
  }
  .sheet {
    width: 1200px; height: 780px;
    display: flex; align-items: center; justify-content: center; gap: 40px;
  }
  .card {
    position: relative;
    width: 540px; height: 309px;
    overflow: hidden;
    box-shadow: 0 8px 24px rgba(0,0,0,0.18);
  }
  /* Front */
  .card-front {
    background: var(--brand-blue);
    display: flex; align-items: center; justify-content: center;
  }
  .brand-mark {
    display: flex; align-items: center; gap: 14px;
  }
  .brand-square {
    width: 34px; height: 34px; background: var(--paper);
  }
  .brand-name {
    font-weight: 800; font-size: 72px; letter-spacing: 2px;
    color: var(--paper); line-height: 1;
  }
  /* Back */
  .card-back { background: var(--paper); }
  .back-brand {
    position: absolute; left: 32px; top: 34px;
    font-weight: 800; font-size: 40px; letter-spacing: 1px;
    color: var(--brand-blue); line-height: 1;
  }
  .accent-tab {
    position: absolute; right: 0; top: 36px;
    width: 20px; height: 40px; background: var(--sky-blue);
  }
  .person {
    position: absolute; right: 34px; top: 36px; text-align: right;
  }
  .person-name {
    font-weight: 700; font-size: 25px; color: var(--brand-blue); line-height: 1.1;
  }
  .person-role {
    font-size: 13px; color: var(--ink); margin-top: 2px;
  }
  .divider {
    position: absolute; left: 32px; right: 28px; top: 112px;
    height: 1px; background: var(--ink);
  }
  .contact-list {
    position: absolute; left: 32px; top: 130px; list-style: none;
  }
  .contact-list li {
    display: flex; align-items: center; gap: 8px;
    font-size: 12.5px; color: var(--ink); height: 22px;
  }
  .contact-icon { width: 13px; height: 13px; flex: none; }
  .address {
    position: absolute; right: 32px; top: 132px; text-align: right;
    font-size: 12.5px; line-height: 1.45; color: var(--ink);
  }
  .swoosh { position: absolute; left: 0; top: 0; }
</style>
</head>
<body>
<main class="sheet">
  <section class="card card-front" aria-label="Card front">
    <div class="brand-mark">
      <span class="brand-square"></span>
      <span class="brand-name">TOVRIN</span>
    </div>
  </section>

  <section class="card card-back" aria-label="Card back">
    <svg class="swoosh" width="540" height="309" viewBox="0 0 540 309" aria-hidden="true">
      <path d="M250 309 C340 250 430 205 540 190 L540 200 C450 215 370 260 300 309 Z" fill="var(--sky-blue)"/>
      <path d="M318 309 C390 262 460 225 540 205 L540 309 Z" fill="var(--brand-blue)"/>
    </svg>

    <div class="back-brand">TOVRIN</div>
    <span class="accent-tab"></span>
    <div class="person">
      <div class="person-name">Warren Halbeck</div>
      <div class="person-role">General Manager</div>
    </div>
    <div class="divider"></div>

    <ul class="contact-list">
      <li>
        <svg class="contact-icon" viewBox="0 0 16 16" aria-hidden="true"><circle cx="8" cy="8" r="8" fill="var(--sky-blue)"/><path d="M5 4.5l1.6-.4 1 2-1 .8a5 5 0 0 0 2.5 2.5l.8-1 2 1-.4 1.6c-3.5 0-6.5-3-6.5-6.5z" fill="#fff"/></svg>
        0472 915 348
      </li>
      <li>
        <svg class="contact-icon" viewBox="0 0 16 16" aria-hidden="true"><circle cx="8" cy="8" r="8" fill="var(--sky-blue)"/><rect x="3.5" y="5" width="9" height="6" fill="#fff"/><path d="M3.5 5l4.5 3.5L12.5 5" stroke="var(--sky-blue)" fill="none"/></svg>
        www.tovrin.com.au
      </li>
      <li>
        <svg class="contact-icon" viewBox="0 0 16 16" aria-hidden="true"><circle cx="8" cy="8" r="8" fill="var(--sky-blue)"/><circle cx="8" cy="8" r="4.5" fill="none" stroke="#fff"/><path d="M3.5 8h9M8 3.5c-2 2.5-2 6.5 0 9M8 3.5c2 2.5 2 6.5 0 9" stroke="#fff" fill="none"/></svg>
        Warren.halbeck@tovrin.com.au
      </li>
    </ul>

    <address class="address" style="font-style:normal">
      87 Marrow Ave,<br>Pendlebay, QLD, 4023
    </address>
  </section>
</main>
</body>
</html>
```